Classy, Elegant, Simple Business Card Design

Looking to have a classy, simple, and elegant design. Want a top notch designed business card. I really like the look of the new torvane credit card. I also like the design I attached. I am trying to reach 21-29 year old females for booking us for there wedding or event. We offer Disc Jockey Service, Photo Booth Rentals, and Uplighting .

Target Market(s)

21-28 year old females

Contact Information for Business Card

Has to have logo, website, email, and phone number

Font styles to use
Other font styles liked:
• open to font choice, modern, clean
Designer to choose
33a6d7
0791cd
0555a3
ffffff

Requirements
Must have
• Has to have logo, website, email, and phone number
Nice to have
• I really like the design of the new torvane credit card. I also included my logo and some designs I like
Should not have
• clutter or too much info

```html
<!DOCTYPE html>
<html lang="en">
<head>
<meta charset="utf-8">
<title>Tidewell Event Group – Business Card</title>
<link rel="stylesheet" href="https://fonts.googleapis.com/css2?family=Montserrat:wght@400;500;600&family=Work+Sans:wght@400;500&display=swap">
<style>
  :root {
    --navy: #13305a;
    --blue: #0555a3;
    --bright: #0791cd;
    --sky: #33a6d7;
    --white: #ffffff;
    --ink: #3a3f47;
    --stage: #e9ecf0;
  }
  * { box-sizing: border-box; margin: 0; padding: 0; }
  html, body { width: 1200px; height: 912px; overflow: hidden; }
  body {
    background: var(--stage);
    font-family: "Work Sans", sans-serif;
    position: relative;
  }
  .card {
    position: absolute;
    left: 290px;
    width: 620px;
    height: 354px;
    border-radius: 22px;
    overflow: hidden;
    box-shadow: 0 10px 30px rgba(19, 48, 90, 0.18);
  }
  .card--back { top: 60px; background: var(--navy); }
  .card--front { top: 494px; background: var(--white); }

  .brand {
    font-family: "Montserrat", sans-serif;
    font-weight: 600;
    letter-spacing: 0.06em;
    text-transform: uppercase;
    display: flex;
    align-items: center;
    gap: 12px;
    white-space: nowrap;
  }
  .brand__dot { width: 18px; height: 18px; border-radius: 50%; flex: none; }

  .card--back .brand {
    position: absolute; top: 140px; left: 0; right: 0;
    justify-content: center;
    color: var(--white);
    font-size: 30px;
  }
  .card--back .brand__dot { background: var(--sky); }
  .card--back .site {
    position: absolute; bottom: 40px; left: 0; right: 0;
    text-align: center;
    color: var(--white);
    font-family: "Montserrat", sans-serif;
    font-size: 16px;
    letter-spacing: 0.08em;
  }

  .wave { position: absolute; inset: 0; width: 100%; height: 100%; }
  .card--front .brand {
    position: absolute; top: 202px; left: 40px;
    color: var(--blue);
    font-size: 24px;
  }
  .card--front .brand__dot { background: var(--bright); }

  .person { position: absolute; top: 120px; right: 36px; text-align: right; }
  .person__name {
    font-family: "Montserrat", sans-serif;
    font-weight: 500;
    font-size: 22px;
    color: var(--bright);
    text-transform: uppercase;
    white-space: nowrap;
  }
  .person__role { font-size: 13px; color: var(--ink); margin-top: 2px; }
  .divider {
    position: absolute; top: 182px; right: 36px; width: 250px;
    height: 1px; background: var(--bright);
  }
  .address {
    position: absolute; top: 196px; right: 36px;
    text-align: right; font-size: 14px; line-height: 1.5; color: var(--ink);
  }
  .rule {
    position: absolute; top: 258px; left: 40px; width: 300px;
    height: 1px; background: var(--bright);
  }
  .contacts { position: absolute; top: 270px; left: 40px; list-style: none; }
  .contacts li {
    display: flex; align-items: center; gap: 10px;
    font-size: 14px; line-height: 22px; color: var(--ink);
  }
  .contacts svg { width: 12px; height: 12px; flex: none; fill: none; stroke: var(--blue); stroke-width: 2; }
  .contacts .accent { color: var(--bright); font-weight: 500; }
</style>
</head>
<body>
  <section class="card card--back">
    <div class="brand"><span class="brand__dot"></span>Tidewell Events</div>
    <p class="site">www.tidewellevents.com</p>
  </section>

  <section class="card card--front">
    <svg class="wave" viewBox="0 0 620 354" preserveAspectRatio="none" aria-hidden="true">
      <path d="M0 0 H620 V24 C520 40 440 80 320 96 C200 112 80 118 0 150 Z" fill="var(--navy)"/>
      <path d="M620 24 C520 40 440 80 320 96 C200 112 80 118 0 150 V160 C80 128 200 122 320 106 C440 90 520 50 620 34 Z" fill="var(--bright)"/>
      <path d="M620 37 C520 53 440 93 320 109 C200 125 80 131 0 163 V168 C80 136 200 130 320 114 C440 98 520 58 620 42 Z" fill="var(--blue)"/>
    </svg>

    <div class="brand"><span class="brand__dot"></span>Tidewell Events</div>

    <div class="person">
      <p class="person__name">Daniel Rourke</p>
      <p class="person__role">Managing Partner</p>
    </div>
    <div class="divider"></div>
    <p class="address">48 Harbor Lane<br>Fairview, CA 90210</p>

    <div class="rule"></div>
    <ul class="contacts">
      <li><svg viewBox="0 0 12 12"><path d="M2 1 L4.5 1 L5 4 L3.5 5 C4 7 5 8 7 8.5 L8 7 L11 7.5 V10 C6 11 1 6 2 1 Z"/></svg><span>555-014-2290</span></li>
      <li><svg viewBox="0 0 12 12"><rect x="1" y="2.5" width="10" height="7"/><path d="M1 2.5 L6 6.5 L11 2.5"/></svg><span>hello@tidewellevents.com</span></li>
      <li><svg viewBox="0 0 12 12"><circle cx="6" cy="6" r="5"/><path d="M1 6 H11 M6 1 C3.5 4 3.5 8 6 11 M6 1 C8.5 4 8.5 8 6 11"/></svg><span>www.<span class="accent">tidewellevents</span>.com</span></li>
    </ul>
  </section>
</body>
</html>
```